Request for Business Card Design

Hi. My name is Marlene, I am looking for a new business card design for my company, Quarrow Signal Instruments, LLC. I really like the design you did for Tarsel Venture and was hoping you could do something similar using our full logo and our mark. I am also open to any raised texture design using our mark. I have attached our full logo, which would need to be somewhere on the card, as well as the mark in both outline and full form, as well as our brand colors / guide. The card does not have to be white, as long as our logo and mark appear. I actually like darker colored business cards more, but am open to all options. If you are interested in working with me, please let me know. We would also take the business card design into letterhead design if you can do that.

```html
<!DOCTYPE html>
<html lang="en">
<head>
<meta charset="utf-8">
<title>Quarrow Signal Instruments – Business Card</title>
<link rel="stylesheet" href="https://fonts.googleapis.com/css2?family=Archivo:wght@400;600;800&family=Arimo:ital,wght@0,400;0,700;1,400&display=swap">
<style>
  :root {
    --stage: #141414;
    --card-dark: #232323;
    --card-dark-deep: #1b1b1b;
    --paper: #f7f6f2;
    --brand-blue: #0093bb;
    --ink: #1a1a1a;
    --muted: #6d6d6d;
    --white: #ffffff;
  }
  * { margin: 0; padding: 0; box-sizing: border-box; }
  html, body {
    width: 1200px; height: 963px; overflow: hidden;
    background: var(--stage);
  }
  .sheet {
    width: 1200px; height: 963px;
    display: flex; align-items: center; justify-content: center; gap: 40px;
  }
  .card {
    position: relative; width: 540px; height: 309px;
    border-radius: 18px; overflow: hidden;
    border-bottom: 4px solid var(--brand-blue);
  }

  /* Front */
  .card-front { background: var(--paper); }
  .front-art { position: absolute; inset: 0; }
  .wordmark { position: absolute; left: 36px; top: 30px; }
  .wordmark-name {
    font-family: "Archivo", sans-serif; font-weight: 800;
    font-size: 38px; letter-spacing: 3px; line-height: 1; color: var(--ink);
  }
  .wordmark-tag {
    font-family: "Archivo", sans-serif; font-weight: 600;
    font-size: 10.5px; letter-spacing: 1.6px; color: var(--ink); margin-top: 3px;
  }
  .person { position: absolute; left: 0; top: 110px; padding-left: 36px; }
  .person::before {
    content: ""; position: absolute; left: 0; top: 2px;
    width: 22px; height: 22px; background: var(--brand-blue);
  }
  .person-name {
    font-family: "Arimo", sans-serif; font-weight: 700;
    font-size: 19px; letter-spacing: 0.5px; color: var(--brand-blue);
  }
  .person-role {
    font-family: "Arimo", sans-serif; font-style: italic;
    font-size: 13px; color: var(--muted); margin-top: 2px;
  }
  .contact {
    position: absolute; left: 36px; top: 178px; list-style: none;
    font-family: "Arimo", sans-serif; font-size: 13px; color: var(--muted); line-height: 1.45;
  }
  .contact-address { margin-left: 22px; margin-bottom: 4px; }
  .contact li { display: flex; align-items: center; gap: 8px; }
  .contact svg { width: 14px; height: 14px; flex: none; }

  /* Back */
  .card-back { background: var(--card-dark); }
  .back-texture { position: absolute; inset: 0; }
  .back-lockup {
    position: absolute; left: 150px; top: 118px;
    display: flex; align-items: center; gap: 14px;
  }
  .lockup-dot { width: 46px; height: 46px; border-radius: 50%; background: var(--brand-blue); }
  .lockup-name {
    font-family: "Archivo", sans-serif; font-weight: 800;
    font-size: 34px; letter-spacing: 3px; line-height: 1; color: var(--white);
  }
  .lockup-tag {
    font-family: "Archivo", sans-serif; font-weight: 600;
    font-size: 9.5px; letter-spacing: 1.5px; color: var(--white); margin-top: 3px;
  }
</style>
</head>
<body>
<main class="sheet">

  <section class="card card-front" aria-label="Card front">
    <svg class="front-art" viewBox="0 0 540 309" role="img" aria-label="Large brand mark area in blue over a dark corner">
      <path d="M540 120 L540 309 L300 309 Q470 300 540 120 Z" fill="var(--card-dark)"/>
      <circle cx="400" cy="215" r="170" fill="var(--white)"/>
      <circle cx="392" cy="212" r="162" fill="var(--brand-blue)"/>
    </svg>

    <div class="wordmark">
      <div class="wordmark-name">QUARROW</div>
      <div class="wordmark-tag">SIGNAL INSTRUMENTS</div>
    </div>

    <div class="person">
      <div class="person-name">DORIAN VALE</div>
      <div class="person-role">Manager</div>
    </div>

    <ul class="contact">
      <li class="contact-address">48 Ferris Lane, Aldon<br>Oregon, 97310</li>
      <li>
        <svg viewBox="0 0 16 16" aria-hidden="true"><path d="M4 1.5l2.2 3-1.3 1.6c.8 1.9 2.2 3.3 4.1 4.1l1.6-1.3 3 2.2-1.1 2.4C7.5 13.8 2.2 8.5 1.5 3.3z" fill="var(--brand-blue)"/></svg>
        541-608-3927
      </li>
      <li>
        <svg viewBox="0 0 16 16" aria-hidden="true"><rect x="1.5" y="3.5" width="13" height="9" fill="none" stroke="var(--brand-blue)" stroke-width="1.4"/><path d="M1.5 3.5l6.5 5 6.5-5" fill="none" stroke="var(--brand-blue)" stroke-width="1.4"/></svg>
        dorian@quarrow.com
      </li>
      <li>
        <svg viewBox="0 0 16 16" aria-hidden="true"><circle cx="8" cy="8" r="6.5" fill="none" stroke="var(--brand-blue)" stroke-width="1.3"/><ellipse cx="8" cy="8" rx="2.8" ry="6.5" fill="none" stroke="var(--brand-blue)" stroke-width="1.1"/><path d="M1.5 8h13" stroke="var(--brand-blue)" stroke-width="1.1"/></svg>
        www.quarrowsignal.com
      </li>
    </ul>
  </section>

  <section class="card card-back" aria-label="Card back">
    <svg class="back-texture" viewBox="0 0 540 309" preserveAspectRatio="none" role="img" aria-label="Raised tonal pattern of the brand mark across the card">
      <defs>
        <linearGradient id="back-sheen" x1="0" y1="0" x2="1" y2="1">
          <stop offset="0" stop-color="var(--card-dark)"/>
          <stop offset="1" stop-color="var(--card-dark-deep)"/>
        </linearGradient>
      </defs>
      <rect width="540" height="309" fill="url(#back-sheen)"/>
    </svg>

    <div class="back-lockup">
      <div class="lockup-dot"></div>
      <div>
        <div class="lockup-name">QUARROW</div>
        <div class="lockup-tag">SIGNAL INSTRUMENTS</div>
      </div>
    </div>
  </section>

</main>
</body>
</html>
```